Design wireframe of E-commerce website *

We are a European online shoe store located in Sweden. The project is to redesign the first page of our e-commerce website https://vantrel.se/skor
We want to receive creative ideas of what our website could look like while keeping all the functions and flows. The new design should be simple, lean and modern.
Specifications:
We have several guidelines for what we are expecting
- Redesign the frontend of our website first page https://vantrel.se/skor and the child page https://www.vantrel.se/skor/dam
- You need to provide a complete clickable wireframe of the target pages.
- All existing components should be in the new design.
- The pages should include all sections: header, footer, product lists and widgets. The page structure of the site should look as the example: https://www.pellimark.co.uk/shoes
- The design must be responsive and Mobile First which can be read from all browsers and different devices.
- You need to have in mind that we really want it to be mobile first, meaning
the mobile view is the most important one
- The new design should reflect our brands essence and come along with the new brandprofiles (fonts, icons...). For example http://brandprofile.pellimark.com/, but keep the logo and colour of the existing Vantrel theme.
- The design should be user friendly.
- The design should be simple enough that the pages can be downloaded fast.
- The new design should look fashionable and be able to generating attracting
traffic.
- The text on the child page https://www.vantrel.se/skor/dam should be handled in a better way and make it easier for users to know which page they are looking at. You can see the example at https://www.pellimark.co.uk/shoes/women but we are open to your good ideas as well.
- We do not want shelves in the design. Pellimark has it, but Vantrel
should not.
- We want to keep the existing responsive sizes for product list which means 2, 4 or 6 pairs of shoes per row.
Practical Information:
We are located in Sweden and have working hours between 9:00 -12:00 (CEST)
Monday - Friday. We have limited capacity to answer every question you have
but will try to get back to you in our working hours as much as we can then
hopefully this can help you get a better understanding of what we are
looking for.
Future Possibilities:We are going to redesign the whole site
of https://www.vantrel.se/skor so the winner
will have the chance to do all the pages in the near future. We are
actively seeking designers for future collaborations on a long-term basis
and it is possible to create a partnership if your work is impressive
enough. *

```html
<!DOCTYPE html>
<html lang="sv">
<head>
<meta charset="utf-8">
<title>Vantrel – Skor</title>
<link href="https://fonts.googleapis.com/css2?family=Open+Sans:wght@400;600;700;800&family=Oswald:wght@500;600&display=swap" rel="stylesheet">
<style>
:root{
  --navy:#1c2434;
  --navy-dark:#141a26;
  --green:#86ad6c;
  --green-dark:#5f8d44;
  --title-green:#72a651;
  --card:#efefef;
  --line:#d8d8d8;
  --text:#333;
  --muted:#888;
  --white:#fff;
}
*{box-sizing:border-box;margin:0;padding:0}
html,body{width:1200px;height:3740px;overflow:hidden}
body{position:relative;background:var(--white);font-family:"Open Sans",Arial,sans-serif;color:var(--text)}
.section{position:absolute;left:0;width:1200px}
.wrap{position:absolute;left:132px;width:936px}

/* header */
.site-header{top:0;height:68px;background:var(--navy)}
.logo{position:absolute;left:132px;top:18px;color:var(--white);font-weight:800;font-size:26px;letter-spacing:1px}
.main-nav{position:absolute;right:132px;top:0;height:68px;display:flex;align-items:center;gap:22px}
.main-nav a{color:var(--white);text-decoration:none;font-size:13px;font-weight:700;letter-spacing:1px;padding:8px 14px}
.main-nav a.active{background:var(--navy-dark)}
.nav-circle{width:22px;height:22px;border-radius:50%;background:var(--white);display:inline-block;opacity:.9}

/* hero */
.hero{top:68px;height:480px;background:linear-gradient(120deg,#c9a850 0%,#8a8a62 35%,#5e6b63 60%,#3b4550 100%)}
.size-filter{position:absolute;left:132px;top:124px;width:256px;padding:16px;background:var(--navy);display:flex;flex-direction:column;gap:14px}
.size-select{height:40px;background:var(--white);font-size:11px;font-weight:700;color:#555;padding:0 12px;display:flex;align-items:center;justify-content:space-between}
.hero-arrow{position:absolute;top:220px;width:24px;height:40px}
.hero-arrow.left{left:20px}.hero-arrow.right{right:20px}

/* categories */
.categories{top:560px;height:272px}
.cat-grid{display:grid;grid-template-columns:repeat(6,140px);column-gap:19px;row-gap:24px}
.cat-tile{height:124px;background:var(--green);display:flex;align-items:center;justify-content:center;color:var(--white);font-weight:800;font-size:13px;letter-spacing:.5px;border:2px solid #a7c893}

/* banner */
.banner{top:856px;height:364px}
.banner .wrap{height:364px;background:linear-gradient(100deg,#8a6a4d 0%,#6a4326 40%,#3e2818 75%,#bba58a 100%)}
.banner-title{position:absolute;left:28px;top:150px;color:var(--white);font-weight:700;font-size:46px}
.btn-shop{position:absolute;left:28px;top:222px;background:var(--white);color:var(--text);font-size:12px;font-weight:700;padding:9px 14px}

/* section titles */
.divider{position:absolute;left:132px;width:936px;height:1px;background:var(--line)}
.section-title{position:absolute;left:0;width:1200px;text-align:center;font-weight:800;font-size:30px;letter-spacing:1px}
.section-title.green{color:var(--title-green)}
.sort-select{position:absolute;top:1280px;width:130px;height:26px;border:1px solid #ccc;font-size:10px;color:#777;padding:0 8px;display:flex;align-items:center;justify-content:space-between}

/* products */
.product-grid{display:grid;grid-template-columns:repeat(5,160px);column-gap:34px;row-gap:24px}
.product-card{height:240px;background:var(--card);text-align:center;padding-top:14px}
.product-img{width:132px;height:110px;margin:0 auto 12px;border-radius:40% 40% 12% 12%/60% 60% 20% 20%}
.product-brand{font-weight:700;font-size:13px}
.product-desc{font-size:10px;color:var(--muted);margin:4px 10px 10px;line-height:1.3;height:26px}
.product-price{font-weight:700;font-size:13px}
.shoe-dark{background:linear-gradient(#3a3a3a,#111)}
.shoe-white{background:linear-gradient(#fafafa,#cfd3d8)}
.shoe-brown{background:linear-gradient(#8b5a34,#4a2c17)}
.shoe-pink{background:linear-gradient(#e079b6,#b53a86)}
.shoe-red{background:linear-gradient(#d63c4a,#7d1520)}
.shoe-green{background:linear-gradient(#7eb068,#3e6b31)}
.shoe-tan{background:linear-gradient(#d9b07a,#a37440)}
.shoe-grey{background:linear-gradient(#a8b3bf,#5d6772)}

/* pagination */
.pagination{position:absolute;top:2158px;left:0;width:1200px;display:flex;justify-content:center;gap:10px}
.page{width:28px;height:28px;border:1px solid #ccc;font-size:11px;display:flex;align-items:center;justify-content:center;color:#666}
.page.current{background:var(--title-green);color:var(--white);border-color:var(--title-green)}
.page.wide{width:44px;border:none}

/* news */
.news-item{position:absolute;top:2300px;width:452px;height:328px}
.news-title{position:absolute;font-family:Oswald,"Arial Narrow",sans-serif;font-weight:600;font-size:48px;line-height:1.05;color:var(--white);letter-spacing:1px}
.news-a{left:132px;background:linear-gradient(90deg,#4c6d85 0%,#6f8ea3 50%,#b9413f 80%,#e0dad2 100%)}
.news-b{left:616px;background:linear-gradient(90deg,#e8e6e2 0%,#c8c3bb 50%,#b07a4c 100%)}
.news-b .news-title{color:var(--navy)}

/* favourites */
.fav-grid .product-card{height:248px}

/* audience */
.audience-item{position:absolute;top:3048px;width:300px;height:212px;display:flex;align-items:flex-end;justify-content:center;padding-bottom:14px;color:var(--white);font-weight:700;font-size:18px}
.aud-women{left:132px;background:linear-gradient(#caa78a,#3a2a22)}
.aud-men{left:450px;background:linear-gradient(#5d6f86,#1d2532)}
.aud-kids{left:768px;background:linear-gradient(#8fa3a8,#3f4b52)}

/* brands */
.brand-strip{top:3328px;height:144px;background:#f7f7f7;display:flex;align-items:center;justify-content:center;gap:46px}
.brand-name{font-weight:700;font-size:22px;color:#555}

/* footer */
.site-footer{top:3488px;height:252px;background:var(--navy);color:#c9ced6;font-size:12px}
.footer-col{position:absolute;top:36px;line-height:1.8}
.footer-col h4{color:var(--white);font-size:12px;font-weight:700;margin-bottom:4px}
.newsletter-input{width:250px;height:30px;background:var(--white);margin-top:6px;font-size:10px;color:#888;padding:0 10px;display:flex;align-items:center;justify-content:space-between}
.newsletter-btn{width:12px;height:10px;background:var(--navy)}
.copyright{position:absolute;left:132px;top:200px;font-size:10px;color:#9aa1ad}
.footer-social{position:absolute;left:846px;top:192px;display:flex;gap:8px;align-items:center}
.footer-social span{width:20px;height:20px;border-radius:50%;background:#4a90d6}
.pay-name{position:absolute;left:960px;top:192px;color:var(--white);font-weight:700;font-size:16px}
</style>
</head>
<body>

<header class="section site-header">
  <div class="logo">VANTREL</div>
  <nav class="main-nav">
    <a class="active" href="#">DAM</a>
    <a href="#">HERR</a>
    <a href="#">BARN</a>
    <span class="nav-circle"></span><span class="nav-circle"></span><span class="nav-circle"></span>
  </nav>
</header>

<section class="section hero" role="img" aria-label="Woman tying the laces of a red running shoe on a sunlit road">
  <div class="size-filter">
    <div class="size-select">WOMEN'S SIZES <span>▾</span></div>
    <div class="size-select">MEN'S SIZES <span>▾</span></div>
    <div class="size-select">KIDS SIZES <span>▾</span></div>
  </div>
  <svg class="hero-arrow left" viewBox="0 0 24 40"><path d="M18 6 L6 20 L18 34" fill="none" stroke="#fff" stroke-width="4"/></svg>
  <svg class="hero-arrow right" viewBox="0 0 24 40"><path d="M6 6 L18 20 L6 34" fill="none" stroke="#fff" stroke-width="4"/></svg>
</section>

<section class="section categories">
  <div class="wrap cat-grid">
    <div class="cat-tile">STÖVLETTER</div>
    <div class="cat-tile">SNEAKERS</div>
    <div class="cat-tile">FINSKOR</div>
    <div class="cat-tile">SANDALER</div>
    <div class="cat-tile">SPORTSKOR</div>
    <div class="cat-tile">SLACSKOR</div>
    <div class="cat-tile">STÖVLAR</div>
    <div class="cat-tile">LOAFERS</div>
    <div class="cat-tile">SANDALER</div>
    <div class="cat-tile">GUMMISTÖVLAR</div>
    <div class="cat-tile">BALLERINA</div>
    <div class="cat-tile">TOFFLOR</div>
  </div>
</section>

<section class="section banner">
  <div class="wrap" role="img" aria-label="Hand polishing a brown leather monk-strap shoe with a brush">
    <div class="banner-title">Aliquam erat</div>
    <div class="btn-shop">SHOP NOW</div>
  </div>
</section>

<div class="divider" style="top:1252px"></div>
<div class="sort-select" style="left:132px">Sortera efter <span>▾</span></div>
<h2 class="section-title green" style="top:1272px">OUR PRODUCTS</h2>
<div class="sort-select" style="left:938px">Visa: Populära <span>▾</span></div>

<section class="section" style="top:1332px">
  <div class="wrap product-grid">
    <div class="product-card"><div class="product-img shoe-dark" role="img" aria-label="Black running shoe"></div><div class="product-brand">Arvelo</div><div class="product-desc">Gel Löparsko i Svart Mesh</div><div class="product-price">950 kr</div></div>
    <div class="product-card"><div class="product-img shoe-white" role="img" aria-label="White leather sneaker"></div><div class="product-brand">Stridal Originals</div><div class="product-desc">Vit Sneaker i Läder</div><div class="product-price">849 kr</div></div>
    <div class="product-card"><div class="product-img shoe-dark" role="img" aria-label="Black slip-on shoe"></div><div class="product-brand">Holmke</div><div class="product-desc">Svart Slip-On Bekväm Sko</div><div class="product-price">649 kr</div></div>
    <div class="product-card"><div class="product-img shoe-brown" role="img" aria-label="Brown ankle boot"></div><div class="product-brand">Sollberg</div><div class="product-desc">Brun Stövlett i Mocka</div><div class="product-price">375 kr</div></div>
    <div class="product-card"><div class="product-img shoe-dark" role="img" aria-label="Black sports shoe"></div><div class="product-brand">Kestrow</div><div class="product-desc">Lätt Träningssko för Dam</div><div class="product-price">999 kr</div></div>

    <div class="product-card"><div class="product-img shoe-white" role="img" aria-label="Light blue canvas sneaker"></div><div class="product-brand">Corvane</div><div class="product-desc">Klassisk Canvas Sneaker Ljusblå</div><div class="product-price">649 kr</div></div>
    <div class="product-card"><div class="product-img shoe-brown" role="img" aria-label="Brown strap sandal"></div><div class="product-brand">Brenholt</div><div class="product-desc">Sandal med Två Remmar</div><div class="product-price">849 kr</div></div>
    <div class="product-card"><div class="product-img shoe-pink" role="img" aria-label="Pink high-top sneaker"></div><div class="product-brand">Relvo</div><div class="product-desc">Rosa Högsko Sneaker Dam</div><div class="product-price">649 kr</div></div>
    <div class="product-card"><div class="product-img shoe-brown" role="img" aria-label="Heeled sandal"></div><div class="product-brand">Espen Lund Sandal</div><div class="product-desc">Klacksandal i Brunt Läder</div><div class="product-price">375 kr</div></div>
    <div class="product-card"><div class="product-img shoe-red" role="img" aria-label="Red high-top sneaker"></div><div class="product-brand">Relvo</div><div class="product-desc">Röd Sneaker med Snörning</div><div class="product-price">999 kr</div></div>

    <div class="product-card"><div class="product-img shoe-brown" role="img" aria-label="Brown flat sandal"></div><div class="product-brand">Golden Comfort</div><div class="product-desc">Platt Sandal i Läder</div><div class="product-price">950 kr</div></div>
    <div class="product-card"><div class="product-img shoe-green" role="img" aria-label="Green sandal"></div><div class="product-brand">Naturel</div><div class="product-desc">Grön Sandal med Spänne</div><div class="product-price">849 kr</div></div>
    <div class="product-card"><div class="product-img shoe-dark" role="img" aria-label="Black strap sandal"></div><div class="product-brand">Tallmark</div><div class="product-desc">Svart Sandal Justerbar Rem</div><div class="product-price">649 kr</div></div>
    <div class="product-card"><div class="product-img shoe-dark" role="img" aria-label="Black loafer"></div><div class="product-brand">Kelso</div><div class="product-desc">Svart Loafer i Skinn</div><div class="product-price">375 kr</div></div>
    <div class="product-card"><div class="product-img shoe-grey" role="img" aria-label="Grey sneaker"></div><div class="product-brand">stridal</div><div class="product-desc">Grå Sneaker med Mocka</div><div class="product-price">999 kr</div></div>
  </div>
</section>

<div class="pagination">
  <span class="page">‹</span><span class="page current">1</span><span class="page">2</span><span class="page">3</span><span class="page">4</span><span class="page">5</span><span class="page wide">…</span><span class="page">100</span><span class="page">›</span>
</div>

<div class="divider" style="top:2212px"></div>
<h2 class="section-title" style="top:2246px">NEWS</h2>
<article class="news-item news-a" role="img" aria-label="Pair of red canvas sneakers on a blue wooden floor">
  <div class="news-title" style="left:24px;top:40px">ETIAM<br>MATTIS<br>AUGUE</div>
</article>
<article class="news-item news-b" role="img" aria-label="Legs in brown suede ankle boots against a light wall">
  <div class="news-title" style="left:24px;top:40px">PROIN<br>DOLOR<br>MAURIS</div>
</article>

<div class="divider" style="top:2672px"></div>
<h2 class="section-title" style="top:2694px">FAVOURITES</h2>
<section class="section fav-grid" style="top:2752px">
  <div class="wrap product-grid">
    <div class="product-card"><div class="product-img shoe-pink" role="img" aria-label="Pink heeled sandal"></div><div class="product-brand">Arvelo</div><div class="product-desc">Rosa Klacksandal för Fest</div><div class="product-price">950 kr</div></div>
    <div class="product-card"><div class="product-img shoe-tan" role="img" aria-label="Beige wedge sandal"></div><div class="product-brand">Stridal Originals</div><div class="product-desc">Beige Kilklack Sandal Dam</div><div class="product-price">849 kr</div></div>
    <div class="product-card"><div class="product-img shoe-tan" role="img" aria-label="Tan sandal"></div><div class="product-brand">Holmke</div><div class="product-desc">Ljusbrun Sandal med Rem</div><div class="product-price">649 kr</div></div>
    <div class="product-card"><div class="product-img shoe-dark" role="img" aria-label="Black sandal"></div><div class="product-brand">Sollberg</div><div class="product-desc">Svart Sandal i Skinn</div><div class="product-price">375 kr</div></div>
    <div class="product-card"><div class="product-img shoe-brown" role="img" aria-label="Dark brown ballerina"></div><div class="product-brand">Kestrow</div><div class="product-desc">Mörkbrun Ballerina med Rosett</div><div class="product-price">999 kr</div></div>
  </div>
</section>

<a class="audience-item aud-women" role="img" aria-label="Woman's legs in high heels">Womens</a>
<a class="audience-item aud-men" role="img" aria-label="Man's legs in dress shoes">Mens</a>
<a class="audience-item aud-kids" role="img" aria-label="Child's feet in sneakers">Kids</a>

<section class="section brand-strip">
  <span class="brand-name">Altora</span>
  <span class="brand-name">Ravik</span>
  <span class="brand-name">Lynxa</span>
  <span class="brand-name">Kestel</span>
  <span class="brand-name">Stridewell</span>
  <span class="brand-name">Paywise</span>
  <span class="brand-name">Northwind</span>
</section>

<footer class="section site-footer">
  <div class="footer-col" style="left:132px">
    Always all shoes in stock<br>
    Always 30 days open purchase<br>
    Always free shipping and free return<br>
    Always price guarantee
  </div>
  <div class="footer-col" style="left:440px">
    <h4>ARE YOU WONDERING ABOUT SOMETHING?</h4>
    Call us at 08 - 410 226 90<br>
    Send us a mail to kundservice@vantrel.se
  </div>
  <div class="footer-col" style="left:818px">
    <h4>Newsletter</h4>
    <div class="newsletter-input">Your e-mail address <span class="newsletter-btn"></span></div>
  </div>
  <div class="copyright">Copyright © 2016 Vantrel. All rights reserved</div>
  <div class="footer-social"><span></span><span></span><span></span></div>
  <div class="pay-name">Kvitta</div>
</footer>

</body>
</html>
```